A website where experts collaborate on your project

I am building a new website where experts (yes, like designers) collaborate on projects with the project owner. More minds = more collaboration = better end product. Please see Pelmora(dot)com for a quick landing page I created for collaborating on presentations (although there will be many project types offered)

I am looking for a DESIGNER LONG TERM, but for now, just need initial mock ups to show the web programmers.

I have 21 Word documents loosely designed, what I would like to see here is a theme. Please DO NOT GO OFF WHAT YOU CURRENTLY SEE AT PELMORA. What is up now is only a quick landing page.

You can view a Word doc of the homepage here:
https://www.filevanta.com/s/qx83kdm2/home.docx?dl=0

WHAT AM I LOOKING FOR?
A clean, well designed theme.

Here is a link to the logo:
https://www.filevanta.com/s/mr47tpz9/logo%20-%20horizontal.tif?dl=0
-----------------------------------------
Here are a few sites I like the design of and what I like about them:
www.quenbrook.com-all around my favorite, beautiful graphics, clean layout, bold use of colors on a dark background
Ravelto.com- clean layout, The use of humans and bubble style elements.
Mintharbor.com :) clean, bold, unique pop art style but professional
plumevault.com - From the unique colors and artwork and the ability of that art to not interfere with the important elements of the site
sparkwidgets.com-clean, nice colors, well organized and separated sections.
www.dunmereco.com-love the font, use of colors and sectionalized style

All in all, I am not picky and open to so many styles. I would ultimately like the designer I pick to design all 21 pages.
Updates

Hello everyone,Moving forward, I would like you all to pay special attention to the section in my brief titled "Here are a few sites I like the design of and what I like about them". Please see below, I handpicked each one of these as sites I really like. Thank you.Here are a few sites I like the design of and what I like about them:Ravelto.com- clean layout, The use of humans and bubble style elements.Mintharbor.com :) clean, bold, unique pop art style but professionalwriteraccess.com - From the unique colors and artwork and the ability of that art to not interfere with the important elements of the sitegrowthgeeks.com-clean, nice colors, well organized and separated sections.www.dunmereco.com-love the font, use of colors and sectionalized stylewww.quenbrook.com-beautiful graphics, clean layout, bold use of colors----------------------------------------- Added Tuesday, November 24, 2015

I updated the homepage, you can see it here:https://www.dropbox.com/s/kwlkbsookq3cg2m/1new%20homepage.docx?dl=0I am modeling it after my favorite designed site: triplelift.comI love the dark colors with the orange glowing style boldness of the buttons. It's real clean too. Added Tuesday, November 24, 2015

Target Market(s)

small business owners, marketers, freelancer writers, graphic designers,

Industry/Entity Type

Building

Number of Pages Required

5+ page

Requirements
Must have
• I can't think of anything the project must have.
Nice to have
• WHAT AM I LOOKING FOR?
• A clean, well designed theme. I had a designer do a bit of work putting elements together, I found it to be very plain, but I like the Application Page (https://www.filevanta.com/s/jb19ckr3/Pelmora-Website.ai?dl=0)
• Here is a link to the logo:
• https://www.filevanta.com/s/mr47tpz9/logo%20-%20horizontal.tif?dl=0
• Here are a few sites I like the design of and what I like about them:
• Ravelto.com- clean layout, The use of humans and bubble style elements.
• Mintharbor.com :) clean, bold, unique pop art style but professional
• plumevault.com - From the unique colors and artwork and the ability of that art to not interfere with the important elements of the site
• sparkwidgets.com-clean, nice colors, well organized and separated sections.
• www.dunmereco.com-love the font, use of colors and sectionalized style
• www.quenbrook.com-beautiful graphics, clean layout, bold use of colors
• -----------------------------------------
Should not have
• out of the boxed, templated style website. I want this site to be memorable and not look like a thousand others

```html
<!DOCTYPE html>
<html lang="en">
<head>
<meta charset="utf-8">
<title>Pelmora – The Evolution of Feedback</title>
<link href="https://fonts.googleapis.com/css2?family=Open+Sans:wght@400;600;700&display=swap" rel="stylesheet">
<style>
  :root {
    --orange: #f39a1e;
    --orange-dark: #d9830f;
    --ink: #222222;
    --muted: #555555;
    --white: #ffffff;
    --hero-top: #3c4650;
    --hero-bottom: #2b3322;
    --works-top: #32465e;
    --works-bottom: #1f3048;
    --dark-band: #1e2227;
    --footer: #2a2b2d;
  }
  * { box-sizing: border-box; margin: 0; padding: 0; }
  html, body { width: 677px; height: 1200px; overflow: hidden; background: var(--white); }
  body { font-family: "Open Sans", Arial, sans-serif; color: var(--ink); }
  .page { position: relative; width: 677px; height: 1200px; overflow: hidden; }
  .abs { position: absolute; }

  /* Hero */
  .hero { left: 0; top: 0; width: 677px; height: 380px;
    background: linear-gradient(180deg, var(--hero-top) 0%, #4a5560 45%, #3a4530 75%, var(--hero-bottom) 100%); }
  .brand { left: 55px; top: 26px; display: flex; align-items: center; gap: 8px; }
  .brand-name { font-size: 19px; font-weight: 600; color: var(--orange); }
  .brand-dot { width: 26px; height: 26px; border-radius: 50%; background: var(--orange); }
  .menu-toggle { left: 605px; top: 24px; width: 16px; }
  .menu-toggle span { display: block; height: 3px; background: var(--white); border-radius: 1px; margin-bottom: 3px; }
  .hero-title { left: 0; width: 677px; top: 114px; text-align: center; color: var(--white); font-size: 26px; font-weight: 700; letter-spacing: .3px; }
  .hero-sub { left: 0; width: 677px; top: 162px; text-align: center; color: var(--white); font-size: 17.5px; line-height: 29px; }
  .btn-outline { top: 252px; width: 131px; height: 34px; border: 2px solid var(--orange); color: var(--white); font-size: 12px; display: flex; align-items: center; justify-content: center; letter-spacing: .3px; }
  .btn-post { left: 176px; }
  .btn-how { left: 360px; }
  .slide-arrow { top: 172px; }
  .slide-prev { left: 20px; }
  .slide-next { left: 641px; }

  /* How it works */
  .works { left: 0; top: 366px; width: 677px; height: 260px;
    background: radial-gradient(circle at 50% 40%, #5e7390 0%, var(--works-top) 45%, var(--works-bottom) 100%); }
  .works-panel { left: 82px; top: 397px; width: 527px; height: 200px; background: rgba(255,255,255,.07); }
  .works-title { left: 0; width: 677px; top: 419px; text-align: center; color: var(--white); font-size: 17px; letter-spacing: .4px; }
  .works-rule { left: 230px; top: 454px; width: 217px; height: 1px; background: var(--white); }
  .works-intro { left: 0; width: 677px; top: 478px; text-align: center; color: var(--white); font-size: 9.5px; font-weight: 600; }
  .step { width: 140px; text-align: center; color: var(--white); font-size: 7.5px; font-weight: 700; line-height: 14px; }
  .step svg { display: block; margin: 0 auto 8px; }
  .step-post { left: 115px; top: 518px; }
  .step-collab { left: 270px; top: 518px; }
  .step-revise { left: 426px; top: 518px; }

  /* Project types */
  .projects-title { left: 55px; top: 661px; color: var(--orange); font-size: 12.5px; font-weight: 600; letter-spacing: .2px; }
  .projects-rule { left: 55px; top: 684px; width: 62px; height: 2px; background: var(--muted); }
  .projects-copy { left: 55px; top: 700px; width: 230px; font-size: 6.6px; line-height: 14.5px; color: var(--muted); }
  .projects-copy p + p { margin-top: 9px; }
  .btn-solid { background: var(--orange); color: var(--white); font-size: 7.5px; font-weight: 600; display: flex; align-items: center; justify-content: center; box-shadow: 0 2px 0 var(--orange-dark); border-radius: 2px; }
  .btn-projects { left: 55px; top: 842px; width: 104px; height: 25px; }
  .devices { left: 305px; top: 650px; width: 372px; height: 258px; }

  /* Benefits */
  .benefits { left: 0; top: 922px; width: 677px; height: 220px;
    background: linear-gradient(180deg, #2a2f35 0%, var(--dark-band) 100%); }
  .benefits-headline { left: 55px; top: 990px; width: 290px; color: var(--white); font-size: 19px; font-weight: 700; line-height: 33px; letter-spacing: .3px; }
  .benefits-title { left: 362px; top: 963px; color: var(--orange); font-size: 11.5px; letter-spacing: .2px; }
  .benefits-intro { left: 362px; top: 986px; width: 260px; color: var(--white); font-size: 6.6px; line-height: 13px; }
  .benefit { color: var(--white); font-size: 6.6px; display: flex; align-items: center; gap: 9px; }
  .benefit svg { flex: none; }
  .btn-read { left: 364px; top: 1078px; width: 80px; height: 22px; gap: 4px; }

  /* Footer */
  .footer { left: 0; top: 1140px; width: 677px; height: 60px; background: var(--footer); }
  .copyright { left: 56px; top: 1170px; color: var(--white); font-size: 7.5px; }
  .footer-links { left: 262px; top: 1171px; color: var(--white); font-size: 7.5px; }
  .social { top: 1164px; width: 22px; height: 22px; border-radius: 2px; }
  .social-1 { left: 496px; background: #3b5b99; }
  .social-2 { left: 530px; background: #2a9fd8; }
  .social-3 { left: 565px; background: #e8711d; }
  .social-4 { left: 599px; background: #d14130; }
</style>
</head>
<body>
<div class="page">

  <!-- Hero -->
  <section class="abs hero" role="img" aria-label="Photo of a joyful businessman leaping in a green field under a cloudy sky"></section>
  <div class="abs brand"><span class="brand-name">pelmora</span><span class="brand-dot"></span></div>
  <div class="abs menu-toggle" aria-label="Menu"><span></span><span></span><span></span></div>
  <h1 class="abs hero-title">THE EVOLUTION OF FEEDBACK</h1>
  <p class="abs hero-sub">Improve your ROI and get new ideas by collaborating<br>with Pelmora's experts</p>
  <a class="abs btn-outline btn-post">POST PROJECT</a>
  <a class="abs btn-outline btn-how">HOW IT WORKS</a>
  <svg class="abs slide-arrow slide-prev" width="14" height="18" viewBox="0 0 14 18"><path d="M10 3 L4 9 L10 15" fill="none" stroke="#fff" stroke-width="2.5"/></svg>
  <svg class="abs slide-arrow slide-next" width="14" height="18" viewBox="0 0 14 18"><path d="M4 3 L10 9 L4 15" fill="none" stroke="#fff" stroke-width="2.5"/></svg>

  <!-- How it works -->
  <section class="abs works" role="img" aria-label="Photo of a businessman touching a glowing digital interface with soft bubble lights"></section>
  <svg class="abs" style="left:0;top:352px" width="677" height="30" viewBox="0 0 677 30"><path d="M0 12 Q170 30 340 18 Q510 4 677 18 L677 0 L0 0 Z" fill="#2e3628"/></svg>
  <svg class="abs" style="left:0;top:600px" width="677" height="30" viewBox="0 0 677 30"><path d="M0 20 Q340 0 677 24 L677 30 L0 30 Z" fill="#ffffff"/></svg>
  <div class="abs works-panel"></div>
  <h2 class="abs works-title">HOW IT WORKS</h2>
  <div class="abs works-rule"></div>
  <p class="abs works-intro">FOR BUSINESSES THAT NEED ACTIONABLE FEEDBACK ON ALL TYPES OF DIGITAL AND PRINT MATERIAL</p>
  <div class="abs step step-post">
    <svg width="26" height="26" viewBox="0 0 26 26"><rect x="3" y="6" width="17" height="17" rx="3" fill="none" stroke="#fff" stroke-width="2"/><path d="M8 14 l3 3 l5 -6" fill="none" stroke="#fff" stroke-width="2"/><path d="M18 3 l5 5" stroke="#fff" stroke-width="2"/></svg>
    POST YOUR PROJECT
  </div>
  <div class="abs step step-collab">
    <svg width="26" height="26" viewBox="0 0 26 26"><g fill="#fff"><circle cx="6" cy="5" r="3"/><circle cx="20" cy="5" r="3"/><circle cx="6" cy="20" r="3"/><circle cx="20" cy="20" r="3"/></g><path d="M6 9 L20 17 M20 9 L6 17" stroke="#fff" stroke-width="2"/></svg>
    COLLABORATE WITH<br>OUR EXPERTS
  </div>
  <div class="abs step step-revise">
    <svg width="26" height="26" viewBox="0 0 26 26"><rect x="2" y="8" width="22" height="14" rx="2" fill="#fff"/><rect x="9" y="4" width="8" height="5" rx="1" fill="none" stroke="#fff" stroke-width="2"/><rect x="2" y="13" width="22" height="1.5" fill="#3a4d66"/></svg>
    REVISE YOUR MATERIAL
  </div>

  <!-- Project types -->
  <h2 class="abs projects-title">PROJECTS TYPES</h2>
  <div class="abs projects-rule"></div>
  <div class="abs projects-copy">
    <p>Has ad platonem hendrerit, in dicat facilisis gloriatur eos. Ut vel nulla nemore utroque, alia graeci corpora ex sit. Ex per quod diceret, assum delectus efficiantur ut usu, sed ei corrumpit dignissim. Reque minim pro in Has ad platonem hendrerit, in dicat facilisis gloriatur eos. Ut vel nulla nemore utroque, alia graeci corpora ex sit.</p>
    <p>Has ad platonem hendrerit, in dicat facilisis gloriatur eos. Ut vel nulla nemore utroque, alia graeci corpora ex sit. Ex per quod diceret, assum delectus efficiantur ut usu.</p>
  </div>
  <a class="abs btn-solid btn-projects">VIEW MORE PROJECTS</a>
  <svg class="abs devices" viewBox="0 0 372 258" role="img" aria-label="Phone and tablet showing print project screens with architectural drawings">
    <defs><linearGradient id="tabletFill" x1="0" y1="0" x2="1" y2="1"><stop offset="0" stop-color="#2b3f8f"/><stop offset="1" stop-color="#162660"/></linearGradient></defs>
    <rect x="115" y="2" width="257" height="254" rx="14" fill="#e4e6e8"/>
    <rect x="135" y="22" width="220" height="212" fill="url(#tabletFill)"/>
    <rect x="3" y="5" width="112" height="233" rx="16" fill="#1c1c1c"/>
    <rect x="11" y="32" width="96" height="176" fill="#ffffff"/>
  </svg>

  <!-- Benefits -->
  <section class="abs benefits" role="img" aria-label="Dark photo of hands working with a network diagram"></section>
  <svg class="abs" style="left:0;top:905px" width="677" height="24" viewBox="0 0 677 24"><path d="M0 0 L677 0 L677 18 Q340 10 0 20 Z" fill="#ffffff"/></svg>
  <h2 class="abs benefits-headline">QUO LUDUS SCRIPSERIT PERSEQUERIS QUO LUDUS SCRIPSERITPERSEQ</h2>
  <h3 class="abs benefits-title">BENEFITS OF EXPERT FEEDBACK</h3>
  <p class="abs benefits-intro">Quo ludus scripserit persequeris te, eos et convenire assentior inciderint. Ridens epicuri hendrerit sit ei, vis at nobis pericula</p>
  <div class="abs benefit" style="left:362px;top:1022px"><svg width="8" height="8" viewBox="0 0 8 8"><path d="M4 1 a3 3 0 1 1 -2 5 l-1 1.5 v-3 a3 3 0 0 1 3 -3.5z" fill="none" stroke="#fff" stroke-width=".8"/></svg>Denique vulputate at est.</div>
  <div class="abs benefit" style="left:362px;top:1042px"><svg width="8" height="8" viewBox="0 0 8 8"><path d="M4 1 a3 3 0 1 1 -2 5 l-1 1.5 v-3 a3 3 0 0 1 3 -3.5z" fill="none" stroke="#fff" stroke-width=".8"/></svg>Denique vulputate at est.</div>
  <div class="abs benefit" style="left:362px;top:1062px"><svg width="8" height="8" viewBox="0 0 8 8"><path d="M4 1 a3 3 0 1 1 -2 5 l-1 1.5 v-3 a3 3 0 0 1 3 -3.5z" fill="none" stroke="#fff" stroke-width=".8"/></svg>Cum ne esse</div>
  <div class="abs benefit" style="left:484px;top:1022px"><svg width="8" height="8" viewBox="0 0 8 8"><path d="M4 1 a3 3 0 1 1 -2 5 l-1 1.5 v-3 a3 3 0 0 1 3 -3.5z" fill="none" stroke="#fff" stroke-width=".8"/></svg>Eum ei modo deleniti maiestatis</div>
  <div class="abs benefit" style="left:484px;top:1042px"><svg width="8" height="8" viewBox="0 0 8 8"><path d="M4 1 a3 3 0 1 1 -2 5 l-1 1.5 v-3 a3 3 0 0 1 3 -3.5z" fill="none" stroke="#fff" stroke-width=".8"/></svg>Ut per impedit oportere mediocritatem</div>
  <a class="abs btn-solid btn-read"><svg width="7" height="7" viewBox="0 0 8 8"><path d="M4 1 a3 3 0 1 1 -2 5 l-1 1.5 v-3 a3 3 0 0 1 3 -3.5z" fill="none" stroke="#fff" stroke-width=".9"/></svg>READ MORE</a>

  <!-- Footer -->
  <footer class="abs footer"></footer>
  <p class="abs copyright">© 2015 All rights reserved Pelmora</p>
  <p class="abs footer-links">Contact | Careers | Privacy | Terms of Use</p>
  <span class="abs social social-1"></span>
  <span class="abs social social-2"></span>
  <span class="abs social social-3"></span>
  <span class="abs social social-4"></span>
</div>
</body>
</html>
```